Velantry Guest Event Collateral

Create a double-sided, oversized piece of collateral for a series of guest networking events that we'll be hosting in 2019

We are looking for this piece of collateral to be the size of an oversized post card (1/2 of an 8/5 x 11 piece of paper). The front should include the following: Velantry's Mission Statement: Continually foster a culture of community and education for focused business professionals. How do we do it? Using four distinct principles, Velantry offers business professionals the opportunity to be successful right now ,as well as next year. Through in-person meetings, virtual meetings, networking events, and educational opportunities Velantry offers members a chance to hit their goals not only this year, but every year! Collaboration: Work with like-minded, driven Velantry members to collaborate and overcome the objections, hurdles and challenges that all business professionals face, either in person at twice monthly meetings, or virtually, from the comfort of your home or office. Accountability: Stay on track, and complete the goals you have set for yourself! Weekly in person or virtual meetings afford all members the opportunity to review their plan twice a month with fellow Velantry members, and trained Velantry coaches. Referrals: In the midst of crafting an executable, measurable and attainable plan let Velantry build your business through a steady stream of referrals via six yearly networking events, specifically designed to ensure you walk away with new referral partners. Strategy: Let Velantry assist you in crafting a strategy within our proven business planning template; realistic, understandable, measurable, beyond normal, attainable and time bound. The back should include the following: Become a Velantry member for $150/month and join us for 6 Networking Events in 2019 plus much more! We aren’t just about collaboration, accountability and strategy! Creating opportunities for referrals is also a cornerstone of Velantry! To make certain we are delivering on this principle, Velantry will host 6 events throughout 2019, complete with specific activities at each event to ensure you meet everyone in the room, making immediate connects to build your referral network. Join now and put yourself in position for success in 2019! Name: Phone: Email: Company Name: Industry: Position: Credit Card Number: Exp. Date: Testimonials: Overall I think people are lazy. I know I am! The benefits I have found and have come to truly appreciate thru Velantry are a sense of professionalism, accountability and shared enthusiasm. These things break that cycle of laziness for me and, I am sure, many others. When I walk into a meeting I know that positive and helpful feedback is the name of the game. Feedback from others and in many other industries from my own has become a key and cornerstone to my business and personal success. I would urge anyone no matter what your occupation to attend a couple of meetings and see how this group of like minded professionals can help you to achieve more. More time, More success, More health, More security, More money, More happiness..............What could you use more of? Desmond K. Ferrow Sr. Automotive Consultant Brookmere Motors & Rentals Thank you!

Target Market(s)

Small business owners, entrpreneurs, networkers, sales people

Industry/Entity Type

Business Consultant

Font styles to use
Sans Serif

Colors
f36f22
f68d4e
f8ba93
f78f20
faa54b

Requirements
Must have
• - Imagery
• - Our company logo
• - Clear CTA to check out our website (www.velantry-example.com)
• - Option to "Join the Velantry Community Today!" and include a spot for someone to fill in their name, email address, company name, and phone number
• - Reference that we host 6+ networking events in Denver throughout the year that are free to attend and are unlike any other networking event they've attended before
• - Mention that we have in-person meetings 2x per month, virtual meeting options, networking events, and educational events
• - Highlight the following acronym which references our core company components:
• Collaboration:
• Work with like-minded, driven Velantry members to collaborate and overcome the objections, hurdles and challenges that all business professionals face, in either in person twice monthly meetings, or virtually, from the comfort of your home of office.
• Accountability:
• Stay on track, and complete the goals you have set for yourself! Weekly in person or virtual meetings afford all members the opportunity to review their plan twice a month with your fellow Velantry members and trained Velantry coaches, to make certain you success is continuous throughout the year.
• Referrals:
• In the midst of crafting an executable, measurable and attainable plan let Velantry build your business through a steady stream of referral opportunities via twelve yearly networking events, specifically designed to ensure you walk away with new referral partners.
• Strategy:
• Let Velantry assist you in crafting a strategy within our proven business planning template; realistic, understandable, measurable, beyond normal, attainable and time bound.

```html
<!DOCTYPE html>
<html lang="en">
<head>
<meta charset="utf-8">
<title>Velantry Guest Event Collateral</title>
<link rel="stylesheet" href="https://fonts.googleapis.com/css2?family=Montserrat:wght@300;400;500;600;700;800&display=swap">
<style>
:root{
  --orange:#f36f22;
  --orange-mid:#f68d4e;
  --orange-soft:#f8ba93;
  --amber:#f78f20;
  --amber-light:#faa54b;
  --ink:#3a3a3a;
  --ink-soft:#555;
  --paper:#ffffff;
  --stage:#e9e9e9;
}
*{box-sizing:border-box;margin:0;padding:0}
html,body{width:1200px;height:861px;overflow:hidden;background:var(--stage);font-family:"Montserrat",sans-serif;color:var(--ink)}
.stage{position:relative;width:1200px;height:861px}
.sheet{position:absolute;top:158px;width:416px;height:589px;background:var(--paper);overflow:hidden;box-shadow:0 6px 18px rgba(0,0,0,.18)}
.sheet--front{left:166px}
.sheet--back{left:638px}
.sheet__bg{position:absolute;inset:0;background:linear-gradient(135deg,#fff 0%,#f4f4f4 50%,#fff 100%)}
.header-wave{position:absolute;left:0;top:0;width:416px;height:120px}
.brand{position:absolute;left:20px;top:18px;display:flex;align-items:center;gap:5px;z-index:3}
.brand__mark{width:18px;height:18px;background:var(--orange)}
.brand__name{font-size:20px;font-weight:400;color:#4a4a4a;letter-spacing:.3px}

/* front */
.hero-photo{position:absolute;left:208px;top:4px;width:212px;height:212px;border-radius:50%;border:5px solid #444;background:radial-gradient(circle at 55% 45%,#b9c0cc 0%,#7d8597 55%,#4e5566 100%);z-index:2}
.headline{position:absolute;left:22px;top:82px;width:168px;height:124px;border-radius:0 0 12px 12px;background:linear-gradient(180deg,#fff,#ececec);box-shadow:0 8px 10px -6px rgba(0,0,0,.25);padding:30px 0 0 15px;z-index:2}
.headline__lead{font-size:19px;font-weight:400;color:#333;line-height:1}
.headline__key{font-size:23.5px;font-weight:800;color:var(--orange);line-height:1.1;border-top:1.5px solid #333;border-bottom:1.5px solid #333;display:inline-block;margin:2px 0 1px}
.headline__sub{font-size:9.5px;font-weight:600;color:#333}
.section-pill{position:absolute;left:2px;top:220px;width:198px;height:25px;border-radius:0 14px 14px 0;background:linear-gradient(90deg,var(--orange),var(--amber-light));color:#fff;font-size:9.5px;font-weight:700;display:flex;align-items:center;padding-left:10px;border:1.5px solid #fff;box-shadow:0 0 0 1px var(--orange)}
.mission{position:absolute;left:22px;top:251px;width:372px;font-size:5.6px;line-height:1.45;color:#444;text-align:justify}
.mission strong{color:var(--orange);font-weight:700}
.component{position:absolute;width:156px;background:linear-gradient(180deg,#fafafa,#eee);border-radius:0 0 12px 12px;padding:22px 12px 8px 12px}
.component--collab{left:43px;top:290px;height:80px}
.component--account{left:230px;top:290px;height:80px}
.component--referral{left:43px;top:380px;height:80px}
.component--strategy{left:230px;top:380px;height:80px}
.component__icon{position:absolute;left:-6px;top:-5px;width:27px;height:27px;border-radius:50%;background:#fff;box-shadow:0 1px 3px rgba(0,0,0,.25);display:flex;align-items:center;justify-content:center}
.component__title{position:absolute;left:28px;top:4px;font-size:7.5px;font-weight:700;color:#222}
.component__body{font-size:5.2px;line-height:1.45;color:#555;text-align:justify}
.footer-wave{position:absolute;left:0;bottom:0;width:416px;height:140px}
.contact{position:absolute;left:0;bottom:0;width:416px;height:78px;color:#fff}
.contact__line{position:absolute;display:flex;align-items:center;gap:7px;font-size:10px;font-weight:600}
.contact__line--mail{left:64px;top:18px}
.contact__line--web{left:64px;top:36px}
.contact__divider{position:absolute;left:230px;top:14px;width:1px;height:42px;background:rgba(255,255,255,.7)}
.contact__phone{position:absolute;left:247px;top:26px;display:flex;align-items:center;gap:4px;font-size:14px;font-weight:700}

/* back */
.signup{position:absolute;left:42px;top:106px;width:330px;height:101px;border:1.3px solid var(--orange);border-radius:12px;padding:22px 30px 0 20px}
.signup__title{position:absolute;left:50%;top:-10px;transform:translateX(-50%);white-space:nowrap;background:#fff;border:1.3px solid var(--orange);border-radius:10px;padding:4px 9px;font-size:7.4px;font-weight:700;color:#222}
.signup__field{display:flex;font-size:7px;color:#333;height:18.4px;align-items:flex-end}
.signup__field i{flex:1;border-bottom:1px dotted #555;margin:0 0 2px 2px}
.meetings-pill{position:absolute;left:114px;top:216px;width:188px;height:22px;border-radius:12px;background:linear-gradient(90deg,var(--orange),var(--amber-light));color:#fff;font-size:11.5px;font-weight:700;display:flex;align-items:center;justify-content:center}
.meetings-sub{position:absolute;left:0;top:240px;width:416px;text-align:center;font-size:8.6px;line-height:1.3;color:#333}
.meetings{position:absolute;left:27px;top:266px;width:362px;height:192px;border-radius:12px;background:linear-gradient(180deg,#f3f3f3,#e9e9e9);overflow:hidden}
.meetings__list{list-style:none;padding:9px 20px 0 21px}
.meetings__list li{position:relative;font-size:5.5px;line-height:1.35;color:#444;margin-bottom:2.6px;padding-left:8px}
.meetings__list li::before{content:"";position:absolute;left:0;top:1.5px;width:3px;height:3px;border-top:1px solid var(--orange);border-right:1px solid var(--orange);transform:rotate(45deg)}
.testimonial{margin:3px 20px 0 21px;padding-top:4px;border-top:1px solid var(--orange-soft);font-size:5.4px;line-height:1.4;color:#444}
.testimonial__quote{font-style:italic}
.testimonial__by{font-weight:700;color:var(--orange);margin-top:1px}
.meetings__venue{position:absolute;left:0;bottom:0;width:362px;height:31px;background:linear-gradient(90deg,var(--orange),var(--amber-light));color:#fff;font-size:5.6px;font-weight:700;text-align:center;display:flex;align-items:center;justify-content:center;line-height:1.4}
</style>
</head>
<body>
<main class="stage">

  <!-- FRONT -->
  <section class="sheet sheet--front">
    <div class="sheet__bg"></div>
    <svg class="header-wave" viewBox="0 0 416 120" aria-hidden="true">
      <defs>
        <linearGradient id="hdrGray" x1="0" y1="0" x2="1" y2="0"><stop offset="0" stop-color="#d6d6d6"/><stop offset="1" stop-color="#f2f2f2"/></linearGradient>
        <linearGradient id="hdrOrange" x1="0" y1="0" x2="1" y2="0"><stop offset="0" stop-color="#f36f22"/><stop offset=".6" stop-color="#faa54b"/><stop offset="1" stop-color="#f78f20"/></linearGradient>
      </defs>
      <path d="M0 0H416V8C340 2 300 30 230 58C160 86 70 92 0 56Z" fill="url(#hdrGray)"/>
      <path d="M0 50C70 88 160 84 230 56C300 28 345 0 416 6V16C345 10 300 40 230 70C160 100 60 108 0 82Z" fill="url(#hdrOrange)"/>
      <path d="M0 82C60 108 160 100 230 70C300 40 345 10 416 16V20C345 16 300 46 230 76C160 106 60 112 0 88Z" fill="#3a3a3a"/>
    </svg>
    <div class="brand"><span class="brand__mark"></span><span class="brand__name">VELANTRY</span></div>
    <div class="hero-photo" role="img" aria-label="Photo of a laptop keyboard overlaid with a glowing world network of connected points"></div>
    <div class="headline">
      <p class="headline__lead">LEARN SIMPLE</p>
      <p class="headline__key">STRATEGIES</p>
      <p class="headline__sub">TO ENSURE YOUR SUCCESS</p>
    </div>
    <h2 class="section-pill">OUR CORE COMPANY COMPONENTS</h2>
    <p class="mission"><strong>Our mission:</strong> continually foster a culture of community and education for focused business professionals. Through in-person meetings twice a month, virtual meetings, networking events and educational events, Velantry helps members hit their goals not only this year, but every year. We host <strong>6+ free networking events in Denver</strong> each year, unlike any networking event you've attended before.</p>

    <article class="component component--collab">
      <span class="component__icon"><svg width="15" height="15" viewBox="0 0 16 16"><circle cx="8" cy="5" r="2.4" fill="#f36f22"/><circle cx="3.5" cy="7" r="1.8" fill="#f78f20"/><circle cx="12.5" cy="7" r="1.8" fill="#f78f20"/><path d="M4 14c0-3 2-5 4-5s4 2 4 5z" fill="#f36f22"/></svg></span>
      <h3 class="component__title">COLLABORATION:</h3>
      <p class="component__body">Work with like-minded, driven Velantry members to collaborate and overcome the objections, hurdles and challenges that all business professionals face, in either in person twice monthly meetings, or virtually, from the comfort of your home or office.</p>
    </article>
    <article class="component component--account">
      <span class="component__icon"><svg width="15" height="15" viewBox="0 0 16 16"><path d="M1.5 3.5l1.2 1.2 2-2.2M1.5 8.5l1.2 1.2 2-2.2" stroke="#f36f22" stroke-width="1.2" fill="none"/><rect x="6.5" y="3" width="8" height="1.4" fill="#f36f22"/><rect x="6.5" y="8" width="8" height="1.4" fill="#f36f22"/><rect x="6.5" y="12.5" width="8" height="1.4" fill="#f36f22"/><rect x="2" y="12.5" width="2" height="1.4" fill="#f36f22"/></svg></span>
      <h3 class="component__title">ACCOUNTABILITY:</h3>
      <p class="component__body">Stay on track, and complete the goals you have set for yourself! Weekly in person or virtual meetings afford all members the opportunity to review their plan twice a month with your fellow Velantry members and trained Velantry coaches, to make certain your success is continuous throughout the year.</p>
    </article>
    <article class="component component--referral">
      <span class="component__icon"><svg width="15" height="15" viewBox="0 0 16 16"><rect x="2" y="9" width="2" height="5" fill="#f36f22"/><rect x="5.5" y="7" width="2" height="7" fill="#f36f22"/><rect x="9" y="8" width="2" height="6" fill="#f36f22"/><rect x="12.5" y="5" width="2" height="9" fill="#f36f22"/><path d="M2 6l4-3 3 2 5-4" stroke="#f78f20" stroke-width="1.2" fill="none"/></svg></span>
      <h3 class="component__title">REFERRALS:</h3>
      <p class="component__body">In the midst of crafting an executable, measurable and attainable plan let Velantry build your business through a steady stream of referral opportunities via twelve yearly networking events, specifically designed to ensure you walk away with new referral partners.</p>
    </article>
    <article class="component component--strategy">
      <span class="component__icon"><svg width="15" height="15" viewBox="0 0 16 16"><path d="M1 6l7-3 7 3-7 3z" fill="#f36f22"/><path d="M4 8v3c0 1.2 2 2 4 2s4-.8 4-2V8L8 10z" fill="#f36f22"/></svg></span>
      <h3 class="component__title">STRATEGY:</h3>
      <p class="component__body">Let Velantry assist you in crafting a strategy within our proven business planning template; realistic, understandable, measurable, beyond normal, attainable and time bound.</p>
    </article>

    <svg class="footer-wave" viewBox="0 0 416 140" aria-hidden="true">
      <defs><linearGradient id="ftrOrange" x1="0" y1="0" x2="1" y2="0"><stop offset="0" stop-color="#f78f20"/><stop offset="1" stop-color="#e0641e"/></linearGradient></defs>
      <path d="M0 30C90 0 160 30 260 26C340 22 390 8 416 0V140H0Z" fill="#3a3a3a"/>
      <path d="M0 42C90 14 170 40 265 36C345 32 395 16 416 8V140H0Z" fill="#e4e4e4"/>
      <path d="M0 62C100 34 180 60 275 54C350 48 395 30 416 22V140H0Z" fill="url(#ftrOrange)"/>
    </svg>
    <div class="contact">
      <p class="contact__line contact__line--mail"><svg width="14" height="10" viewBox="0 0 14 10"><rect x=".6" y=".6" width="12.8" height="8.8" fill="none" stroke="#fff" stroke-width="1.2"/><path d="M.6.6L7 5.5 13.4.6" fill="none" stroke="#fff" stroke-width="1.2"/></svg>info@velantry-example.com</p>
      <p class="contact__line contact__line--web"><svg width="13" height="13" viewBox="0 0 14 14"><circle cx="7" cy="7" r="6" fill="none" stroke="#fff" stroke-width="1.1"/><ellipse cx="7" cy="7" rx="2.6" ry="6" fill="none" stroke="#fff" stroke-width="1"/><path d="M1 7h12M2 4h10M2 10h10" stroke="#fff" stroke-width=".9"/></svg>www.velantry-example.com</p>
      <span class="contact__divider"></span>
      <p class="contact__phone"><svg width="12" height="12" viewBox="0 0 12 12"><rect width="12" height="12" rx="2" fill="#fff"/><path d="M3.5 2.5l1.6 1.6-.9 1.2c.5 1 1.4 1.9 2.4 2.4l1.2-.9 1.6 1.6-1 1.1C5.7 9.2 2.8 6.3 2.4 3.5z" fill="#e86a20"/></svg>555-014-2290</p>
    </div>
  </section>

  <!-- BACK -->
  <section class="sheet sheet--back">
    <div class="sheet__bg"></div>
    <svg class="header-wave" viewBox="0 0 416 120" aria-hidden="true">
      <path d="M0 0H416V52C340 30 280 50 220 54C150 58 70 50 0 38Z" fill="url(#hdrGray)"/>
      <path d="M0 36C70 50 150 58 220 52C280 48 340 28 416 48V60C340 40 280 60 220 66C150 72 60 68 0 60Z" fill="url(#hdrOrange)"/>
      <path d="M0 60C60 68 150 72 220 66C280 60 340 40 416 60V64C340 46 280 64 220 70C150 76 60 72 0 64Z" fill="#3a3a3a"/>
    </svg>
    <div class="brand"><span class="brand__mark"></span><span class="brand__name">VELANTRY</span></div>

    <form class="signup">
      <h2 class="signup__title">JOIN THE VELANTRY COMMUNITY TODAY!</h2>
      <p class="signup__field">Name:<i></i></p>
      <p class="signup__field">Email Address:<i></i></p>
      <p class="signup__field">Company Name:<i></i></p>
      <p class="signup__field">Phone Number:<i></i></p>
    </form>

    <h2 class="meetings-pill">ABOUT OUR MEETINGS</h2>
    <p class="meetings-sub">What should I expect when attending a<br>Velantry group meeting?</p>

    <div class="meetings">
      <ul class="meetings__list">
        <li>Expect to collaborate with focused business professionals who share your desire to be<br>continually successful</li>
        <li>Expect a casual environment where sharing is encouraged and trust is quickly established</li>
        <li>Expect your time to be utilized efficiently and productively within a one hour time frame</li>
        <li>Expect a professionally trained Velantry representative to run a business meeting</li>
        <li>Expect to be energized, to learn and develop your skills</li>
        <li>Expect to attend two meetings before making a decision to best experience everything<br>Velantry has to offer.</li>
        <li>Expect each meeting to be in a quiet, professional corporate conference room without distractions</li>
        <li>Expect an opportunity to ask questions to see how Velantry can help you in your chosen field</li>
        <li>Expect to be successful!</li>
      </ul>
      <blockquote class="testimonial">
        <p class="testimonial__quote">“I would urge anyone, no matter what your occupation, to attend a couple of meetings and see how this group of like-minded professionals can help you achieve more. More time, more success, more money, more happiness… What could you use more of?”</p>
        <p class="testimonial__by">Desmond K. Ferrow, Sr. Automotive Consultant, Brookmere Motors &amp; Rentals</p>
      </blockquote>
      <p class="meetings__venue">Become a Velantry member for $150/month and join us for 6 Networking Events in 2019 plus much more!<br>All meetings are held from 8:15 am to 9:15 am at Harborline Co-working in the Eastline<br>district at 1200 Example Street Denver 80200</p>
    </div>

    <svg class="footer-wave" viewBox="0 0 416 140" aria-hidden="true">
      <path d="M0 30C90 0 160 30 260 26C340 22 390 8 416 0V140H0Z" fill="#3a3a3a"/>
      <path d="M0 42C90 14 170 40 265 36C345 32 395 16 416 8V140H0Z" fill="#e4e4e4"/>
      <path d="M0 62C100 34 180 60 275 54C350 48 395 30 416 22V140H0Z" fill="url(#ftrOrange)"/>
    </svg>
    <div class="contact">
      <p class="contact__line contact__line--mail"><svg width="14" height="10" viewBox="0 0 14 10"><rect x=".6" y=".6" width="12.8" height="8.8" fill="none" stroke="#fff" stroke-width="1.2"/><path d="M.6.6L7 5.5 13.4.6" fill="none" stroke="#fff" stroke-width="1.2"/></svg>info@velantry-example.com</p>
      <p class="contact__line contact__line--web"><svg width="13" height="13" viewBox="0 0 14 14"><circle cx="7" cy="7" r="6" fill="none" stroke="#fff" stroke-width="1.1"/><ellipse cx="7" cy="7" rx="2.6" ry="6" fill="none" stroke="#fff" stroke-width="1"/><path d="M1 7h12M2 4h10M2 10h10" stroke="#fff" stroke-width=".9"/></svg>www.velantry-example.com</p>
      <span class="contact__divider"></span>
      <p class="contact__phone"><svg width="12" height="12" viewBox="0 0 12 12"><rect width="12" height="12" rx="2" fill="#fff"/><path d="M3.5 2.5l1.6 1.6-.9 1.2c.5 1 1.4 1.9 2.4 2.4l1.2-.9 1.6 1.6-1 1.1C5.7 9.2 2.8 6.3 2.4 3.5z" fill="#e86a20"/></svg>555-014-2290</p>
    </div>
  </section>

</main>
</body>
</html>
```